Business Card for a Jewellery Brand

Business card for an upscale jewellery brand. Attached is the brand logo and icon and color board. I am looking for two card versions: one for the founder and one is generic. The card should be elegant and convey upscale and premium feel. I am open to both square and rectangle card shapes.

Industry/Entity Type

Jewelry

Contact Information for Business Card

Two cards: (1) Sunela Parvaniya (Founder) (2) General
(1) Sunela Parvaniya card should have Name: Sunela Parvaniya, Title: Founder Email id: sunela@quiremo.com.au. Phone no: +61452913307
(2) Generic card should have Email id: info@quiremo.com.au. Phone no: +61436207518

Requirements
Must have
• Workmark
• ICON
• Phone no
• Email ID
• ABN: 58219740312 (Note: ABN is Business number in Australia)
• Website: www.quiremo.com.au
• Instagram: quiremo_jewellery
• Facebook: @quiremojewellery
Nice to have
• Tagline

```html
<!DOCTYPE html>
<html lang="en">
<head>
<meta charset="utf-8">
<title>Quiremo Business Cards</title>
<link href="https://fonts.googleapis.com/css2?family=Lato:wght@400;700&display=swap" rel="stylesheet">
<style>
  :root {
    --backdrop: #2b2b2d;
    --card: #1d2024;
    --rose: #e89b95;
    --rose-soft: #e7a7a1;
    --ink-light: #f1ece9;
    --rule: #c98985;
  }
  * { box-sizing: border-box; margin: 0; padding: 0; }
  html, body {
    width: 1200px;
    height: 1189px;
    overflow: hidden;
    background: var(--backdrop);
    font-family: "Lato", sans-serif;
  }
  .sheet {
    position: relative;
    width: 1200px;
    height: 1189px;
  }
  .card {
    position: absolute;
    left: 160px;
    width: 880px;
    height: 500px;
    background: var(--card);
    border-radius: 26px;
    box-shadow: 0 18px 40px rgba(0,0,0,0.45);
    overflow: hidden;
  }
  .card--front { top: 60px; }
  .card--back { top: 630px; }

  .wordmark {
    color: var(--rose);
    font-weight: 400;
    letter-spacing: 0.32em;
    line-height: 1;
  }

  /* Front */
  .front-brand {
    position: absolute;
    left: 0;
    right: 0;
    top: 170px;
    text-align: center;
  }
  .front-brand .wordmark { font-size: 92px; padding-left: 0.32em; }
  .front-web {
    position: absolute;
    left: 0;
    right: 0;
    top: 310px;
    text-align: center;
    color: var(--rose);
    font-size: 24px;
    letter-spacing: 0.12em;
  }

  /* Back */
  .back-brand {
    position: absolute;
    left: 0;
    top: 0;
    width: 430px;
    height: 500px;
    display: flex;
    flex-direction: column;
    align-items: center;
    justify-content: center;
    gap: 34px;
  }
  .brand-dot {
    width: 64px;
    height: 64px;
    border: 3px solid var(--rose);
    border-radius: 50%;
  }
  .back-brand .wordmark { font-size: 54px; padding-left: 0.32em; }
  .divider {
    position: absolute;
    left: 440px;
    top: 110px;
    width: 1.5px;
    height: 280px;
    background: var(--rule);
  }
  .contact {
    position: absolute;
    left: 486px;
    top: 110px;
    width: 370px;
  }
  .contact__name {
    color: var(--rose);
    font-weight: 700;
    font-size: 30px;
    line-height: 1.1;
  }
  .contact__title {
    color: var(--ink-light);
    font-size: 20px;
    margin-top: 2px;
  }
  .contact__list {
    list-style: none;
    margin-top: 22px;
  }
  .contact__item {
    display: flex;
    align-items: center;
    gap: 12px;
    color: var(--rose-soft);
    font-size: 21px;
    height: 34px;
  }
  .badge {
    flex: none;
    width: 24px;
    height: 24px;
    border-radius: 50%;
    background: var(--ink-light);
    display: flex;
    align-items: center;
    justify-content: center;
  }
  .badge svg { width: 14px; height: 14px; }
  .contact__abn {
    margin-top: 12px;
    font-size: 22px;
    color: var(--rose-soft);
  }
  .contact__abn b { color: var(--ink-light); font-weight: 700; }
</style>
</head>
<body>
<main class="sheet">
  <section class="card card--front" aria-label="Card front">
    <div class="front-brand"><span class="wordmark">QUIREMO</span></div>
    <p class="front-web">www.quiremo.com.au</p>
  </section>

  <section class="card card--back" aria-label="Card back">
    <div class="back-brand">
      <span class="brand-dot"></span>
      <span class="wordmark">QUIREMO</span>
    </div>
    <div class="divider"></div>
    <div class="contact">
      <h1 class="contact__name">Sunela Parvaniya</h1>
      <p class="contact__title">Founder</p>
      <ul class="contact__list">
        <li class="contact__item">
          <span class="badge">
            <svg viewBox="0 0 24 24"><path fill="#1d2024" d="M6.6 10.8a15 15 0 0 0 6.6 6.6l2.2-2.2a1 1 0 0 1 1-.25 11.4 11.4 0 0 0 3.6.57 1 1 0 0 1 1 1V20a1 1 0 0 1-1 1A17 17 0 0 1 3 4a1 1 0 0 1 1-1h3.5a1 1 0 0 1 1 1c0 1.25.2 2.45.57 3.57a1 1 0 0 1-.25 1z"/></svg>
          </span>+61452913307
        </li>
        <li class="contact__item">
          <span class="badge">
            <svg viewBox="0 0 24 24"><rect x="3" y="6" width="18" height="12" rx="1" fill="#1d2024"/><path d="M3.5 6.5 12 13l8.5-6.5" fill="none" stroke="#f1ece9" stroke-width="1.6"/></svg>
          </span>sunela@quiremo.com.au
        </li>
        <li class="contact__item">
          <span class="badge"></span>quiremo_jewellery
        </li>
        <li class="contact__item">
          <span class="badge"></span>@quiremojewellery
        </li>
      </ul>
      <p class="contact__abn"><b>ABN:</b> 58219740312</p>
    </div>
  </section>
</main>
</body>
</html>
```